eBook Cover_H. Lindqvist-Borna
Schnell und zuverlässoig,Änderungswünsche wurden umgehend ausgeführt. Vielen Dank für das tolle Cover zu meinem ersten Buch!
Zielgruppe
freie Roman-Autorin (Erstlingswerk)
Zielgruppe: Lesende (Erwachsene), Frauen
Charakterisierung: magisch-realistischer Familienroman, spielt im Europa der Jetzt-Zeit
Aufgabenstellung
Im ersten Schritt geht es um ein Cover für ein eBook, das aber bei Bedarf als Book on Demand gedruckt werden soll. Es wird daher später Anforderung bzgl. Dicke / Umfang des gedruckten Buches und einer Rückseite geben. Das gewählte Design soll dann dahingehend überarbeitet und finale Druckdaten zur Verfügung gestellt werden. Dies soll von vornherein berücksichtigt werden und im Preis enthalten sein.
Titel: Regen über Glas, Monde im Moos
Autorinnenname: Henrike Lindqvist-Borna
des weiteren auf dem Cover: Roman

```html
<!DOCTYPE html>
<html lang="de">
<head>
<meta charset="utf-8">
<title>Regen über Glas, Monde im Moos – Henrike Lindqvist-Borna</title>
<link rel="stylesheet" href="https://fonts.googleapis.com/css2?family=Cinzel:wght@400;600;700&display=swap">
<style>
  :root {
    --page: #ffffff;
    --night: #04090d;
    --deep: #0a1a22;
    --cloud: #102a33;
    --teal: #2a7080;
    --glow: #6cc4d2;
    --sea: #7fb8c2;
    --shore: #0b161b;
    --ink: #ffffff;
  }
  html, body {
    margin: 0;
    padding: 0;
    width: 848px;
    height: 1200px;
    overflow: hidden;
    background: var(--page);
  }
  .page {
    position: relative;
    width: 848px;
    height: 1200px;
    background: var(--page);
  }
  .cover {
    position: absolute;
    left: 127px;
    top: 107px;
    width: 606px;
    height: 895px;
    overflow: hidden;
    background: var(--night);
    font-family: "Cinzel", "Times New Roman", serif;
    color: var(--ink);
  }
  .cover-art {
    position: absolute;
    inset: 0;
    width: 606px;
    height: 895px;
    display: block;
  }
  .author {
    position: absolute;
    top: 36px;
    left: 0;
    right: 0;
    margin: 0;
    text-align: center;
    font-weight: 700;
    font-size: 23px;
    letter-spacing: 0.5px;
  }
  .title {
    position: absolute;
    top: 128px;
    left: 0;
    right: 0;
    margin: 0;
    text-align: center;
    font-weight: 600;
    font-size: 54px;
    line-height: 66px;
    text-shadow: 0 0 3px rgba(0,0,0,0.7);
  }
  .title .minor {
    font-size: 22px;
  }
  .genre {
    position: absolute;
    top: 818px;
    left: 0;
    right: 0;
    margin: 0;
    text-align: center;
    font-weight: 700;
    font-size: 26px;
    letter-spacing: 0.5px;
  }
</style>
</head>
<body>
  <div class="page">
    <section class="cover">
      <svg class="cover-art" viewBox="0 0 606 895" role="img" aria-label="Nächtlicher Sternenhimmel mit leuchtender Milchstraße über dunklen Wolken und einem Strand, eine Frau im Kleid steht mit erhobenen Armen in den Dünen am Meer">
        <defs>
          <linearGradient id="sky" x1="0" y1="0" x2="0" y2="1">
            <stop offset="0" stop-color="#04090d"/>
            <stop offset="0.35" stop-color="#07141a"/>
            <stop offset="0.55" stop-color="#0c232c"/>
            <stop offset="0.68" stop-color="#0a1c23"/>
            <stop offset="0.72" stop-color="#1a4650"/>
            <stop offset="0.76" stop-color="#3f7f8b"/>
            <stop offset="0.79" stop-color="#163a43"/>
            <stop offset="0.86" stop-color="#0b181d"/>
            <stop offset="1" stop-color="#03070a"/>
          </linearGradient>
          <radialGradient id="milky" cx="0.5" cy="0.5" r="0.5">
            <stop offset="0" stop-color="#7fd2de" stop-opacity="0.75"/>
            <stop offset="0.45" stop-color="#2f8797" stop-opacity="0.45"/>
            <stop offset="1" stop-color="#0a1a22" stop-opacity="0"/>
          </radialGradient>
          <radialGradient id="cloudglow" cx="0.5" cy="0.5" r="0.5">
            <stop offset="0" stop-color="#3b8594" stop-opacity="0.55"/>
            <stop offset="1" stop-color="#0c232c" stop-opacity="0"/>
          </radialGradient>
          <radialGradient id="surf" cx="0.5" cy="0.5" r="0.5">
            <stop offset="0" stop-color="#a6dbe2" stop-opacity="0.7"/>
            <stop offset="1" stop-color="#2a7080" stop-opacity="0"/>
          </radialGradient>
          <radialGradient id="dune" cx="0.5" cy="0.5" r="0.5">
            <stop offset="0" stop-color="#3a5c64" stop-opacity="0.6"/>
            <stop offset="1" stop-color="#0b161b" stop-opacity="0"/>
          </radialGradient>
          <filter id="soft" x="-20%" y="-20%" width="140%" height="140%">
            <feGaussianBlur stdDeviation="18"/>
          </filter>
        </defs>
        <rect width="606" height="895" fill="url(#sky)"/>
        <ellipse cx="560" cy="230" rx="200" ry="120" fill="url(#milky)" transform="rotate(-55 560 230)"/>
        <ellipse cx="520" cy="400" rx="190" ry="90" fill="url(#milky)" transform="rotate(-20 520 400)"/>
        <ellipse cx="420" cy="470" rx="220" ry="70" fill="url(#cloudglow)"/>
        <ellipse cx="150" cy="520" rx="200" ry="60" fill="#050d11" opacity="0.6" filter="url(#soft)"/>
        <ellipse cx="380" cy="660" rx="260" ry="22" fill="url(#surf)"/>
        <ellipse cx="560" cy="648" rx="90" ry="35" fill="#0a1419" opacity="0.8" filter="url(#soft)"/>
        <ellipse cx="340" cy="760" rx="230" ry="55" fill="url(#dune)"/>
      </svg>
      <p class="author">HENRIKE LINDQVIST-BORNA</p>
      <h1 class="title">REGEN <span class="minor">ÜBER</span> GLAS,<br>MONDE <span class="minor">IM</span> MOOS</h1>
      <p class="genre">ROMAN</p>
    </section>
  </div>
</body>
</html>
```